Note/Card sent to show appreciation to partners who worked with us to improve local communities

I'd like a simple note/card designed for a wide audience. Originally, I called this a "Thanksgiving Card," but it's really just a card to be sent around Thanksgiving, not specifically celebrating the Thanksgiving holiday. We plan to send the card out just prior to Thanksgiving 2017 (Nov. 24, 2017). I work at a regulated electric utility, and we'd like to say thank you to the many stakeholders who we partner with throughout the year to support initiatives that help to improve our state and create opportunities for economic growth. I'm interested mostly in the design of the card, not the simple verbiage on the inside.
Target Market(s)
Customers, charitable foundations, nonprofits, advocacy groups, industry associations, friends

```html
<!DOCTYPE html>
<html lang="en">
<head>
<meta charset="utf-8">
<title>Season of Thanks Postcard</title>
<link rel="stylesheet" href="https://fonts.googleapis.com/css2?family=Great+Vibes&family=Josefin+Sans:ital,wght@0,300;1,300&display=swap">
<style>
  :root {
    --backdrop: #ece6d6;
    --paper: #f8f5e2;
    --ink-rust: #8e3b1c;
    --ink-soft: #5e4030;
    --rule: #b3907f;
    --turkey-deep: #c2452a;
    --turkey-mid: #f29a55;
    --turkey-light: #fcd9a4;
    --leaf-warm: #d98c5f;
    --leaf-pale: #f0c79a;
  }
  * { box-sizing: border-box; margin: 0; padding: 0; }
  html, body {
    width: 1006px;
    height: 1200px;
    overflow: hidden;
    background: var(--backdrop);
  }
  .sheet {
    position: relative;
    width: 1006px;
    height: 1200px;
  }
  .card {
    position: absolute;
    left: 73px;
    width: 860px;
    height: 560px;
    background: var(--paper);
    box-shadow: 0 4px 14px rgba(60, 40, 20, 0.18);
    overflow: hidden;
  }
  .card--front { top: 30px; }
  .card--back { top: 610px; }

  .turkey-art {
    position: absolute;
    left: 0;
    top: 0;
    width: 430px;
    height: 560px;
    background:
      radial-gradient(ellipse 26% 22% at 68% 18%, var(--turkey-deep) 0%, rgba(194,69,42,0.7) 55%, rgba(194,69,42,0) 100%),
      radial-gradient(ellipse 70% 60% at 55% 60%, var(--turkey-mid) 0%, rgba(242,154,85,0.75) 50%, rgba(252,217,164,0.4) 85%, rgba(252,217,164,0) 100%),
      linear-gradient(160deg, rgba(246,180,110,0.85) 0%, rgba(252,217,164,0.5) 70%, rgba(252,217,164,0) 100%);
  }

  .tagline {
    position: absolute;
    left: 455px;
    width: 360px;
    top: 214px;
    text-align: center;
    font-family: "Josefin Sans", sans-serif;
    font-weight: 300;
    font-size: 24px;
    color: var(--ink-soft);
  }
  .greeting {
    position: absolute;
    font-family: "Great Vibes", cursive;
    font-size: 52px;
    line-height: 1;
    color: var(--ink-rust);
    white-space: nowrap;
  }
  .card--front .greeting { left: 456px; top: 262px; }
  .card--back .greeting { left: 30px; top: 228px; }

  .swash {
    position: absolute;
    width: 160px;
    height: 40px;
    overflow: visible;
  }
  .card--front .swash { left: 660px; top: 292px; }
  .card--back .swash { left: 234px; top: 258px; }
  .swash path { fill: none; stroke: var(--ink-rust); stroke-width: 1.6; }

  .sender {
    position: absolute;
    left: 60px;
    width: 250px;
    top: 320px;
    text-align: center;
    font-family: "Josefin Sans", sans-serif;
    font-style: italic;
    font-weight: 300;
    font-size: 20px;
    color: var(--ink-soft);
  }

  .divider {
    position: absolute;
    left: 429px;
    top: 48px;
    width: 1.5px;
    height: 354px;
    background: var(--rule);
  }
  .stamp-box {
    position: absolute;
    left: 709px;
    top: 34px;
    width: 121px;
    height: 82px;
    border: 1.5px solid var(--rule);
  }
  .address-lines {
    position: absolute;
    left: 502px;
    top: 215px;
    width: 328px;
    list-style: none;
  }
  .address-lines li {
    height: 47.5px;
    border-top: 1.5px solid var(--rule);
  }

  .leaf-spray {
    position: absolute;
    left: 310px;
    top: 410px;
    width: 290px;
    height: 145px;
    border-radius: 50%;
    background: radial-gradient(ellipse at 50% 50%, var(--leaf-warm) 0%, rgba(240,199,154,0.7) 50%, rgba(240,199,154,0) 75%);
  }
</style>
</head>
<body>
<main class="sheet">
  <section class="card card--front">
    <div class="turkey-art" role="img" aria-label="Watercolour turkey silhouette in orange and rust tones"></div>
    <p class="tagline">In All Things Give Thanks.</p>
    <p class="greeting">Happy Thanksgiving</p>
    <svg class="swash" viewBox="0 0 160 40" aria-hidden="true">
      <path d="M0 36 C40 28 110 40 140 26 C160 16 156 2 146 6"/>
    </svg>
  </section>

  <section class="card card--back">
    <p class="greeting">Happy Thanksgiving</p>
    <svg class="swash" viewBox="0 0 160 40" aria-hidden="true">
      <path d="M0 36 C40 28 110 40 140 26 C160 16 156 2 146 6"/>
    </svg>
    <p class="sender">from all of us at</p>

    <div class="divider"></div>
    <div class="stamp-box"></div>
    <ul class="address-lines">
      <li></li><li></li><li></li><li></li>
    </ul>

    <div class="leaf-spray" role="img" aria-label="Watercolour spray of autumn oak leaves and berries"></div>
  </section>
</main>
</body>
</html>
```